Website Design for a Project Management Consulting Business

I have a logo design already and now I need a website.
I am a project manager and run my own consulting business.
Currently I am under contract with 3 major Vantage 400 companies. I'd like a website I can direct current and future clients.
My job is running IT projects and working with developers to deliver business priorities.
The website should be professional and clean - I work IT projects and would like to incorporate that into any theme.
I'd like the site to have several page or breakoff links - sections would include : about me, about my services, a page to display all of my certification badges, another page to talk about highlights from past projects and so on.
Looking for a collaborative experience.

Industry/Entity Type

Vantage 400 Consulting Firm - Project Management

Coding

Coded - Design and coding required

Number of Pages Required

1 page

Font styles to use
Serif

Colors
0094D4
00A9DD
6FCCEA
C7EBF8
E9F6FB
EE7325
F08F49
F5BC92
FAE3D3
FDF4ED

Requirements
Must have
• Sections that are a must: About Me (bio), About My Services, About my Certifications and Credentials, Experience on Past Projects,
Nice to have
• I have added the logo below - I'd like to use the logo and have it prominent ; should be professional and inviting

```html
<!DOCTYPE html>
<html lang="en">
<head>
<meta charset="utf-8">
<title>Meridian LLC — Project Management Consulting</title>
<link href="https://fonts.googleapis.com/css2?family=Saira:wght@300;400;500&family=Barlow:wght@400;500;600&display=swap" rel="stylesheet">
<style>
:root{
  --blue:#0094D4;
  --blue-bright:#0a7fd8;
  --blue-deep:#0d3a7a;
  --navy:#0a2a5c;
  --ink:#1c2b45;
  --text:#3c4657;
  --muted:#6b7585;
  --sky:#C7EBF8;
  --mist:#E9F6FB;
  --white:#ffffff;
  --line:#d7dde6;
}
*{margin:0;padding:0;box-sizing:border-box}
html,body{width:1200px;height:4155px;overflow:hidden;background:var(--white)}
body{font-family:"Barlow",sans-serif;color:var(--text)}
.page{position:relative;width:1200px;height:4155px;overflow:hidden}
.abs{position:absolute}
.display{font-family:"Saira",sans-serif;font-weight:400;letter-spacing:2px;text-transform:uppercase}

/* header */
.site-header{position:absolute;left:0;top:0;width:1200px;height:88px;background:var(--white)}
.brand{position:absolute;display:flex;align-items:center;gap:12px}
.brand-square{width:30px;height:30px;border:3px solid var(--blue-deep)}
.brand-name{font-family:"Saira",sans-serif;font-weight:500;color:var(--blue-deep);font-size:30px;letter-spacing:1px}
.nav{position:absolute;top:34px;font-family:"Saira",sans-serif;font-size:14px;color:var(--ink);letter-spacing:.5px}
.nav.active{border-bottom:2px solid var(--blue);padding-bottom:6px}
.btn{position:absolute;display:flex;align-items:center;justify-content:center;background:var(--blue);color:var(--white);font-family:"Saira",sans-serif;font-weight:500;letter-spacing:1px;font-size:13px;text-transform:uppercase}
.btn-frame{position:absolute;border:2px solid var(--white)}

/* hero */
.hero{position:absolute;left:0;top:88px;width:1200px;height:596px;background:linear-gradient(100deg,#06203f 0%,#0b3b6e 45%,#1b5fa0 75%,#0d3566 100%)}
.hero-person{position:absolute;left:610px;top:20px;width:390px;height:576px;background:linear-gradient(180deg,#5a7ea8 0%,#6f8fb5 60%,#2f4a6e 100%);border-radius:190px 190px 0 0;opacity:.9}

/* about */
.about-photo-back{position:absolute;left:120px;top:917px;width:305px;height:270px;background:linear-gradient(180deg,var(--blue-bright),#0b58b0)}
.about-photo{position:absolute;left:143px;top:775px;width:382px;height:388px;background:linear-gradient(150deg,#8a7a6a,#4b3f36 60%,#2a2420);border-top-right-radius:160px}
.eyebrow{font-family:"Saira",sans-serif;font-size:16px;letter-spacing:2px;color:var(--blue);text-transform:uppercase}
.h2{font-family:"Saira",sans-serif;font-weight:400;font-size:40px;letter-spacing:2px;color:var(--ink);text-transform:uppercase}
.rule{position:absolute;height:2px;background:var(--blue)}
.body-copy{font-size:17px;line-height:24px;color:var(--text)}

/* services */
.services{position:absolute;left:0;top:1257px;width:1200px;height:813px;background:linear-gradient(180deg,#e8eef5 0%,#dfe8f1 55%,#cfdfee 100%)}
.hex{position:absolute;width:295px;height:340px;clip-path:polygon(50% 0,100% 25%,100% 75%,50% 100%,0 75%,0 25%);background:var(--white);text-align:center}
.hex.featured{background:linear-gradient(180deg,#0b2d63,#0d5fb0)}
.hex-icon{position:absolute;left:50%;transform:translateX(-50%);top:62px}
.hex h3{position:absolute;left:0;right:0;top:150px;font-family:"Barlow",sans-serif;font-weight:600;font-size:15px;color:var(--ink)}
.hex p{position:absolute;left:32px;right:32px;top:178px;font-size:12.5px;line-height:19px;color:var(--muted)}
.hex.featured h3,.hex.featured p{color:var(--white)}
.hex-toggle{position:absolute;left:50%;transform:translateX(-50%);top:262px}

/* projects */
.projects{position:absolute;left:0;top:2070px;width:1200px;height:615px;background:linear-gradient(180deg,#0b72d2,#0a86e0 60%,#1a8fe0)}
.card{position:absolute;overflow:hidden;border-radius:8px}
.card-media{position:absolute;inset:0}
.card-title{position:absolute;left:0;right:0;font-family:"Barlow",sans-serif;font-weight:500;color:var(--white);text-align:center;text-transform:uppercase}
.card-text{position:absolute;left:0;right:0;font-size:14px;color:#e6eefb;text-align:center}

/* certificates */
.badge{position:absolute;border-radius:50%}
.org-label{position:absolute;width:300px;text-align:center;font-size:15px;color:var(--blue)}
.org-name{position:absolute;width:300px;text-align:center;font-size:19px;color:var(--ink)}

/* contact */
.contact{position:absolute;left:0;top:3235px;width:1200px;height:603px;background:linear-gradient(120deg,#0a2f6c 0%,#0c3c82 60%,#0a2e68 100%)}
.contact-media{position:absolute;left:145px;top:35px;width:460px;height:510px;background:linear-gradient(140deg,#4f7fb8,#2e64a8 50%,#1a4f94);clip-path:polygon(0 0,100% 0,100% 100%,0 100%)}
.field{position:absolute;left:678px;width:394px;border-bottom:2px solid #b9c8dd;font-size:13px;color:var(--white);padding:0 3px 18px}

/* footer */
.footer-col-rule{position:absolute;width:1px;background:var(--line)}
.footer-head{position:absolute;font-family:"Saira",sans-serif;font-size:15px;letter-spacing:1px;color:var(--ink);text-transform:uppercase;border-left:3px solid var(--blue);padding-left:16px}
.footer-links{position:absolute;font-size:12.5px;line-height:26px;color:var(--text);list-style:none}
.contact-row{position:absolute;display:flex;gap:10px;align-items:flex-start;font-size:12.5px;line-height:20px;color:var(--text)}
.social{width:28px;height:28px;border-radius:50%;background:var(--blue-bright)}
</style>
</head>
<body>
<div class="page">

  <header class="site-header">
    <div class="brand" style="left:102px;top:24px">
      <div class="brand-square"></div>
      <div class="brand-name">MERIDIAN LLC</div>
    </div>
    <a class="nav active" style="left:440px">ABOUT ME</a>
    <a class="nav" style="left:564px">SERVICES</a>
    <a class="nav" style="left:685px">PROJECTS</a>
    <a class="nav" style="left:812px">CERTIFICATE</a>
    <a class="btn" style="left:969px;top:27px;width:122px;height:36px;border-radius:2px">Contact</a>
  </header>

  <section class="hero">
    <div class="abs" role="img" aria-label="Data centre server room with blue lighting" style="inset:0;background:linear-gradient(90deg,rgba(4,20,44,.55),rgba(4,20,44,0) 60%)"></div>
    <div class="hero-person" role="img" aria-label="Portrait of the consultant in a blue checked suit"></div>
    <div class="abs display" style="left:138px;top:150px;font-size:21px;color:var(--white);letter-spacing:3px">Welcome to Meridian</div>
    <h1 class="abs display" style="left:106px;top:180px;width:470px;text-align:center;font-size:56px;line-height:52px;color:var(--white);letter-spacing:1px;font-weight:400">Project Management Consulting</h1>
    <div class="btn-frame" style="left:236px;top:362px;width:172px;height:46px"></div>
    <a class="btn" style="left:228px;top:354px;width:172px;height:46px">Learn More</a>
  </section>

  <section>
    <div class="about-photo-back" role="img" aria-label="Blue circuit-board texture"></div>
    <div class="about-photo" role="img" aria-label="Portrait photo of the consultant"></div>
    <div class="abs eyebrow" style="left:590px;top:786px">My Bio</div>
    <h2 class="abs h2" style="left:588px;top:800px">About Me</h2>
    <div class="rule" style="left:590px;top:856px;width:70px"></div>
    <p class="abs body-copy" style="left:590px;top:880px;width:490px">Lorem ipsum dolor sit amet, consectetur adipiscing elit, sed do eiusmod tempor incididunt ut labore et dolore magna aliqua. Ut enim ad minim veniam, quis nostrud exercitation ullamco laboris nisi ut aliquip ex ea commodo consequat.</p>
    <p class="abs body-copy" style="left:590px;top:1010px;width:490px">Duis aute irure dolor in reprehenderit in voluptate velit esse cillum dolore eu fugiat nulla pariatur. Excepteur sint occaecat cupidatat non proident, sunt in culpa qu</p>
    <div class="btn-frame" style="left:598px;top:1128px;width:164px;height:40px;border-color:var(--blue)"></div>
    <a class="btn" style="left:590px;top:1120px;width:164px;height:40px">Learn More</a>
  </section>

  <section class="services">
    <div class="abs" role="img" aria-label="Faint city skyline with network lights" style="inset:0;background:linear-gradient(180deg,rgba(255,255,255,0) 40%,rgba(160,196,230,.35) 100%)"></div>
    <h2 class="abs h2" style="left:0;width:1145px;text-align:center;top:50px;font-size:36px">Services Provide</h2>
    <div class="rule" style="left:537px;top:103px;width:72px"></div>

    <div class="hex" style="left:111px;top:125px">
      <svg class="hex-icon" width="60" height="60" viewBox="0 0 60 60" fill="none" stroke="#0a7fd8" stroke-width="2.5"><circle cx="14" cy="16" r="6"/><circle cx="46" cy="16" r="6"/><rect x="20" y="6" width="20" height="16"/><path d="M6 50V30h16M54 50V30H38M18 30h24v20"/></svg>
      <h3>CONSULTING SERVICE</h3>
      <p>Lorem Ipsum is simply dummy text of the printing and typesetting industry. Lorem Ipsum is simply</p>
      <svg class="hex-toggle" width="30" height="30" viewBox="0 0 30 30" fill="none" stroke="#0a7fd8" stroke-width="2"><circle cx="15" cy="15" r="13"/><path d="M10 13l5 5 5-5"/></svg>
    </div>
    <div class="hex featured" style="left:433px;top:125px">
      <svg class="hex-icon" width="60" height="60" viewBox="0 0 60 60" fill="none" stroke="#ffffff" stroke-width="2.5"><circle cx="26" cy="22" r="9"/><circle cx="26" cy="22" r="3"/><path d="M40 12h12M40 20h12M40 28h12M6 46c10-6 22-6 30 0l14-6"/></svg>
      <h3 style="top:140px">PROJECT MANAGEMENT</h3>
      <p style="top:166px">Lorem Ipsum is simply dummy text of the printing and typesetting industry. Lorem Ipsum is simply</p>
      <svg class="hex-toggle" style="top:250px" width="30" height="30" viewBox="0 0 30 30" fill="none" stroke="#ffffff" stroke-width="2"><circle cx="15" cy="15" r="13"/><path d="M10 13l5 5 5-5"/></svg>
    </div>
    <div class="hex" style="left:757px;top:125px">
      <svg class="hex-icon" width="60" height="60" viewBox="0 0 60 60" fill="none" stroke="#0a7fd8" stroke-width="2.5"><circle cx="38" cy="20" r="10"/><circle cx="38" cy="20" r="4"/><path d="M14 26a10 10 0 1 1 10 12v6h-8v-6"/></svg>
      <h3 style="top:140px">IT TRAINING</h3>
      <p style="top:166px">Lorem Ipsum is simply dummy text of the printing and typesetting industry. Lorem Ipsum is simply</p>
      <svg class="hex-toggle" style="top:250px" width="30" height="30" viewBox="0 0 30 30" fill="none" stroke="#0a7fd8" stroke-width="2"><circle cx="15" cy="15" r="13"/><path d="M10 13l5 5 5-5"/></svg>
    </div>
    <div class="hex" style="left:275px;top:405px">
      <svg class="hex-icon" width="64" height="64" viewBox="0 0 64 64" fill="none" stroke="#0a7fd8" stroke-width="2.5"><rect x="4" y="6" width="56" height="40" rx="3"/><path d="M24 58h16M32 46v12"/><circle cx="32" cy="26" r="9"/><circle cx="32" cy="26" r="3"/></svg>
      <h3>LOREM IPSUM</h3>
      <p>Lorem Ipsum is simply dummy text of the printing and typesetting industry. Lorem Ipsum is simply</p>
      <svg class="hex-toggle" width="30" height="30" viewBox="0 0 30 30" fill="none" stroke="#0a7fd8" stroke-width="2"><circle cx="15" cy="15" r="13"/><path d="M10 13l5 5 5-5"/></svg>
    </div>
    <div class="hex" style="left:595px;top:398px">
      <svg class="hex-icon" width="60" height="60" viewBox="0 0 60 60" fill="none" stroke="#0a7fd8" stroke-width="2.5"><path d="M18 56V42c-8-6-10-16-6-24 6-12 26-14 34 0l4 12h-6v10h-8v6"/><circle cx="32" cy="22" r="7"/><circle cx="32" cy="22" r="2.5"/></svg>
      <h3 style="top:145px">LOREM IPSUM</h3>
      <p style="top:172px">Lorem Ipsum is simply dummy text of the printing and typesetting industry. Lorem Ipsum is simply</p>
      <svg class="hex-toggle" style="top:256px" width="30" height="30" viewBox="0 0 30 30" fill="none" stroke="#0a7fd8" stroke-width="2"><circle cx="15" cy="15" r="13"/><path d="M10 13l5 5 5-5"/></svg>
    </div>
  </section>

  <section class="projects">
    <div class="abs" role="img" aria-label="Blue perspective grid backdrop" style="left:0;right:0;bottom:0;height:200px;background:linear-gradient(180deg,rgba(255,255,255,0),rgba(120,190,245,.35))"></div>
    <div class="abs display" style="left:0;width:1210px;text-align:center;top:50px;font-size:16px;color:var(--white)">Recent</div>
    <h2 class="abs h2" style="left:0;width:1220px;text-align:center;top:66px;color:var(--white);font-size:38px">Projects</h2>
    <div class="rule" style="left:576px;top:117px;width:62px;background:var(--white)"></div>

    <div class="card" style="left:139px;top:193px;width:280px;height:280px">
      <div class="card-media" role="img" aria-label="Engineer working in a server room" style="background:linear-gradient(160deg,#1d3c66,#0b1e3a)"></div>
      <div class="card-title" style="top:200px;font-size:18px;padding-right:20px">Lorem Ipsum is</div>
      <div class="card-text" style="top:228px;font-size:13px">Lorem Ipsum has been the in</div>
    </div>
    <div class="card" style="left:780px;top:193px;width:318px;height:280px">
      <div class="card-media" role="img" aria-label="Operations centre with monitoring screens" style="background:linear-gradient(160deg,#1a4a82,#0b2344)"></div>
      <div class="card-title" style="top:200px;font-size:18px;padding-left:60px">s simply dummy</div>
      <div class="card-text" style="top:228px;font-size:13px;padding-left:60px">industry's standard dummy text</div>
    </div>
    <div class="card" style="left:375px;top:157px;width:487px;height:353px;box-shadow:0 10px 30px rgba(0,20,60,.4)">
      <div class="card-media" role="img" aria-label="Two colleagues reviewing a tablet in a data centre" style="background:linear-gradient(160deg,#5b7ea8,#2b4b76 55%,#152a4a)"></div>
      <div class="card-title" style="top:278px;font-size:19px">Lorem Ipsum is simply dummy</div>
      <div class="card-text" style="top:308px">Lorem Ipsum has been the industry's standard dummy text</div>
    </div>

    <svg class="abs" style="left:96px;top:313px" width="26" height="44" viewBox="0 0 26 44" fill="none" stroke="#ffffff" stroke-width="5"><path d="M22 4L5 22l17 18"/></svg>
    <svg class="abs" style="left:1118px;top:313px" width="26" height="44" viewBox="0 0 26 44" fill="none" stroke="#ffffff" stroke-width="5"><path d="M4 4l17 18L4 40"/></svg>
  </section>

  <section>
    <div class="abs eyebrow" style="left:0;width:1200px;text-align:center;top:2752px;font-size:15px">My Certificates</div>
    <h2 class="abs h2" style="left:0;width:1200px;text-align:center;top:2766px;font-size:36px">Certificates</h2>
    <svg class="abs" style="left:260px;top:2848px" width="685" height="40" viewBox="0 0 685 40" fill="none" stroke="#6aa6e0" stroke-width="1.5">
      <path d="M7 4h670M7 4v28M340 4v24M677 4v28"/>
      <circle cx="7" cy="34" r="3.5"/><circle cx="340" cy="30" r="3.5"/><circle cx="677" cy="34" r="3.5"/>
    </svg>

    <div class="badge" style="left:145px;top:2928px;width:112px;height:112px;border:6px solid #4b2a7f;background:var(--white)"></div>
    <div class="badge" style="left:273px;top:2928px;width:112px;height:112px;border:6px solid #4b2a7f;background:var(--white)"></div>
    <div class="badge" style="left:468px;top:2922px;width:120px;height:120px;background:radial-gradient(circle,#f7b43c 55%,#ec9b1f 100%)"></div>
    <div class="badge" style="left:615px;top:2922px;width:120px;height:120px;background:radial-gradient(circle,#f06a3a 55%,#d94e22 100%)"></div>
    <svg class="abs" style="left:798px;top:2920px" width="126" height="126" viewBox="0 0 126 126"><rect x="25" y="25" width="76" height="76" transform="rotate(45 63 63)" fill="#1e3c6b" stroke="#9fb3cc" stroke-width="4"/></svg>
    <svg class="abs" style="left:934px;top:2920px" width="126" height="126" viewBox="0 0 126 126"><rect x="25" y="25" width="76" height="76" transform="rotate(45 63 63)" fill="#1e3c6b" stroke="#9fb3cc" stroke-width="4"/></svg>

    <div class="org-label" style="left:118px;top:3066px">Organization</div>
    <div class="org-name" style="left:118px;top:3088px">Project Leadership Guild</div>
    <div class="org-label" style="left:452px;top:3062px">Organization</div>
    <div class="org-name" style="left:452px;top:3084px">Agile Craft Council</div>
    <div class="org-label" style="left:788px;top:3062px">Organization</div>
    <div class="org-name" style="left:788px;top:3084px">Framework Agile Board</div>
  </section>

  <section class="contact">
    <div class="contact-media" role="img" aria-label="Developer at a laptop overlaid with blue graphics"></div>
    <div class="abs display" style="left:675px;top:115px;font-size:15px;color:var(--white)">Get in touch</div>
    <h2 class="abs h2" style="left:674px;top:128px;color:var(--white);font-size:34px">Contact Me</h2>
    <div class="field" style="top:195px">Name</div>
    <div class="field" style="top:251px">Phone Number</div>
    <div class="field" style="top:307px">Email address</div>
    <div class="field" style="top:362px;padding-bottom:46px">Message</div>
    <a class="btn" style="left:675px;top:457px;width:178px;height:40px;border-radius:2px">Send Enquiry</a>
  </section>

  <footer>
    <div class="brand" style="left:135px;top:3912px">
      <div class="brand-square"></div>
      <div class="brand-name" style="font-size:28px">MERIDIAN LLC</div>
    </div>
    <div class="abs" style="left:142px;top:3995px;display:flex;gap:8px" aria-label="Social links">
      <span class="social"></span><span class="social"></span><span class="social"></span><span class="social"></span>
    </div>
    <div class="abs" style="left:142px;top:4042px;font-size:12px;color:var(--text)">Copyright 2022 Meridian LLC All Right Reserved</div>

    <div class="footer-col-rule" style="left:485px;top:3845px;height:240px"></div>
    <div class="footer-col-rule" style="left:677px;top:3845px;height:240px"></div>
    <div class="footer-col-rule" style="left:862px;top:3845px;height:240px"></div>

    <div class="footer-head" style="left:485px;top:3902px">Navigation</div>
    <ul class="footer-links" style="left:505px;top:3938px"><li>About Me</li><li>Services Provide</li><li>Projects</li><li>Certifications</li></ul>
    <div class="footer-head" style="left:677px;top:3902px">Resources</div>
    <ul class="footer-links" style="left:694px;top:3938px"><li>Support</li><li>Privacy Policy</li><li>Contact Us</li></ul>
    <div class="footer-head" style="left:865px;top:3900px">Contact Us</div>

    <div class="contact-row" style="left:900px;top:3938px">
      <svg width="28" height="28" viewBox="0 0 28 28"><circle cx="14" cy="14" r="14" fill="#0a7fd8"/><path d="M14 7a5 5 0 0 0-5 5c0 4 5 9 5 9s5-5 5-9a5 5 0 0 0-5-5z" fill="#fff"/><circle cx="14" cy="12" r="1.8" fill="#0a7fd8"/></svg>
      <div>2180 Harbor Line Road<br>44 Crescent Avenue, Lakeview</div>
    </div>
    <div class="contact-row" style="left:900px;top:3992px;align-items:center">
      <svg width="28" height="28" viewBox="0 0 28 28"><circle cx="14" cy="14" r="14" fill="#0a7fd8"/><path d="M10 8l3 3-2 2c1 2 3 4 5 5l2-2 3 3-2 2c-5 0-11-6-11-11z" fill="#fff"/></svg>
      <div>(555) 010 4471</div>
    </div>
    <div class="contact-row" style="left:900px;top:4032px;align-items:center">
      <svg width="28" height="28" viewBox="0 0 28 28"><circle cx="14" cy="14" r="14" fill="#0a7fd8"/><rect x="7" y="9" width="14" height="10" fill="#fff"/><path d="M7 9l7 6 7-6" fill="none" stroke="#0a7fd8" stroke-width="1.5"/></svg>
      <div>hello@meridianpm.example</div>
    </div>
  </footer>

</div>
</body>
</html>
```